Calloway needs a modernized design

We would like a modern update (that can be responsive) to our existing website. Attached are the two existing pages we would like new concepts of - our home page and a page about one of our locations.

Calloway is provides executive offices and virtual office services. Startups, law firms, and financial services are our primary clients. We would like a professional, clean design, leaning towards minimalist. We intend to greatly reduce/eliminate the long paragraphs of text.

Requirements
Must have
• A design that can be responsive
Nice to have
• Large image(s) on home page that rotate.

```html
<!DOCTYPE html>
<html lang="en">
<head>
<meta charset="utf-8">
<title>Calloway Business Centers</title>
<link rel="stylesheet" href="https://fonts.googleapis.com/css2?family=Roboto:wght@400;500&family=Lato:wght@400&family=Open+Sans:wght@400&display=swap">
<style>
:root{
  --navy:#07076b;
  --navy-text:#0b0b70;
  --grey-bg:#eeeeee;
  --panel:#efefef;
  --rule:#d4d4d4;
  --body:#7a7a7a;
  --dark:#444;
  --white:#fff;
}
*{box-sizing:border-box;margin:0;padding:0}
html,body{width:1200px;height:2473px;overflow:hidden}
body{position:relative;background:var(--white);font-family:"Open Sans",Arial,sans-serif;color:var(--body)}
.abs{position:absolute}
.topbar{left:0;top:0;width:1200px;height:53px;background:var(--navy)}
.social{display:flex;gap:14px;align-items:center}
.social span{display:block;width:30px;height:30px;border-radius:50%;border:2px solid var(--white)}
.social span:first-child{background:var(--white)}
.topbar .social{position:absolute;left:79px;top:11px}
.phones{position:absolute;right:78px;top:0;height:53px;display:flex;align-items:center;gap:22px;color:var(--white);font:400 17px Roboto,sans-serif}
.phones .item{display:flex;align-items:center;gap:12px}
.header{left:0;top:53px;width:1200px;height:120px}
.brand{position:absolute;left:79px;top:22px;display:flex;align-items:center;gap:14px}
.brand-dot{width:74px;height:74px;border-radius:50%;background:var(--navy)}
.brand-name{font:500 34px Roboto,sans-serif;color:var(--navy-text);letter-spacing:1px}
.nav{position:absolute;left:443px;top:0;height:120px;display:flex;align-items:center;font:400 18px Roboto,sans-serif;color:#666}
.nav a{color:inherit;text-decoration:none;margin-right:28px}
.nav a:last-child{margin-right:0}
.nav a.active{color:var(--navy-text)}
.hero{left:0;top:173px;width:1200px;height:521px;background:linear-gradient(180deg,#d9dfe7 0%,#9aa3b5 45%,#3a4263 100%)}
.hero-title{position:absolute;left:0;width:1200px;top:530px;text-align:center;color:var(--white);font:400 35px Lato,sans-serif;letter-spacing:.5px}
.hero-sub{position:absolute;left:0;width:1200px;top:580px;text-align:center;color:var(--white);font:400 21px Lato,sans-serif}
h2{font:400 43px Roboto,sans-serif;color:var(--navy-text)}
.para{font:400 15px/29px "Open Sans",Arial,sans-serif;color:var(--body)}
.btn{display:flex;align-items:center;justify-content:center;background:var(--navy);color:var(--white);font:400 21px Roboto,sans-serif}
.side-list{left:747px;top:757px;width:375px;height:313px;background:var(--panel)}
.side-list .head{height:62px;background:var(--navy);color:var(--white);font:400 19px Roboto,sans-serif;display:flex;align-items:center;padding-left:23px}
.side-list ul{list-style:none;margin:0 15px}
.side-list li{height:62px;display:flex;align-items:center;padding-left:8px;font:400 15px Roboto,sans-serif;color:#333;border-bottom:1px solid var(--rule)}
.side-list li:last-child{border-bottom:none}
.services{left:0;top:1132px;width:1200px;height:511px;background:var(--grey-bg)}
.video{width:510px;height:208px;top:1318px}
.video.full{left:77px;background:linear-gradient(180deg,#e4e6ea,#c8ccd3)}
.video.virtual{left:612px;background:linear-gradient(180deg,#5f6168,#3c3e46)}
.caption{top:1535px;width:510px;text-align:center;font:400 16px/25px Arial,sans-serif;color:#444;padding:0 20px}
.caption b{font-weight:400;color:var(--navy-text)}
.quote{left:747px;top:1706px;width:375px;height:359px;background:var(--panel)}
.quote .head{height:62px;background:var(--navy);color:var(--white);font:400 21px Roboto,sans-serif;display:flex;align-items:center;justify-content:center}
.field{position:absolute;left:21px;width:333px;height:43px;background:var(--white);font:400 13px Arial,sans-serif;color:#999;padding-left:17px;display:flex;align-items:center}
.quote .submit{position:absolute;left:0;bottom:0;width:375px;height:51px}
.footer{left:0;top:2128px;width:1200px;height:280px;background:var(--grey-bg)}
.foot-head{top:2158px;font:400 21px Roboto,sans-serif;color:var(--navy-text)}
.badge{left:77px;top:2217px;width:182px;height:156px;background:linear-gradient(180deg,#b9bcc4,#8d93a6);border-radius:6px}
.links{top:2206px;font:400 14px Arial,sans-serif;color:#555;list-style:none}
.links li{height:41px;display:flex;align-items:center;gap:17px}
.links li::before{content:"";width:10px;height:10px;border-radius:50%;background:#888}
.links li.current{color:var(--navy-text)}
.links li.marked::before,.links li.current::before{background:var(--navy)}
.contact{left:810px;top:2206px;width:300px;font:400 14px/23px Arial,sans-serif;color:#666}
.contact .row{display:flex;gap:14px;align-items:flex-start;margin-bottom:14px}
.contact .row span{width:258px}
.bottombar{left:0;top:2408px;width:1200px;height:65px;background:var(--navy);color:var(--white)}
.copy{position:absolute;left:79px;top:0;height:65px;display:flex;align-items:center;font:400 14px Arial,sans-serif}
.copy b{font-weight:400;font-size:15px;margin:0 6px}
.bottombar .social{position:absolute;right:78px;top:16px;gap:10px}
.bottombar .social span{width:34px;height:34px}
</style>
</head>
<body>

<div class="abs topbar">
  <div class="social" aria-label="Social links"><span></span><span></span><span></span><span></span><span></span></div>
  <div class="phones">
    <div class="item"><svg width="17" height="17" viewBox="0 0 24 24" fill="#fff"><path d="M6.6 10.8a15 15 0 0 0 6.6 6.6l2.2-2.2c.3-.3.7-.4 1-.2 1.1.4 2.3.6 3.6.6.6 0 1 .4 1 1V20c0 .6-.4 1-1 1A17 17 0 0 1 3 4c0-.6.4-1 1-1h3.5c.6 0 1 .4 1 1 0 1.2.2 2.4.6 3.6.1.3 0 .7-.2 1z"/></svg>214.555.0190</div>
    <span>|</span>
    <div class="item"><svg width="17" height="17" viewBox="0 0 24 24" fill="#fff"><path d="M6.6 10.8a15 15 0 0 0 6.6 6.6l2.2-2.2c.3-.3.7-.4 1-.2 1.1.4 2.3.6 3.6.6.6 0 1 .4 1 1V20c0 .6-.4 1-1 1A17 17 0 0 1 3 4c0-.6.4-1 1-1h3.5c.6 0 1 .4 1 1 0 1.2.2 2.4.6 3.6.1.3 0 .7-.2 1z"/></svg>713.555.0147</div>
  </div>
</div>

<header class="abs header">
  <div class="brand"><div class="brand-dot"></div><div class="brand-name">CALLOWAY</div></div>
  <nav class="nav">
    <a class="active" href="#">HOME</a><a href="#">PROPERTIES</a><a href="#">VIRTUAL TOURS</a><a href="#">PHOTOS</a><a href="#">BROKER REFERRALS</a>
  </nav>
</header>

<div class="abs hero" role="img" aria-label="Photo of business professionals in a meeting"></div>
<div class="hero-title">COST EFFECTIVE VIRTUAL OFFICE SOLUTIONS</div>
<div class="hero-sub">CUSTOMIZED COROPORATE IMAGE</div>

<h2 class="abs" style="left:79px;top:753px">WELCOME TO CALLOWAY</h2>
<p class="abs para" style="left:79px;top:823px;width:650px">Either you need Dallas/Ft. Worth Office Space, Dallas Executive Suites, Ft. Worth Executive Suites, Houston Office Space, Houston Executive Suites, or maybe you simply need a place to stop in and use an on-demand office or meeting room from time to time or utilize our local business phone numbers, phone answering or business addresses through one of our virtual office solutions. At Calloway,.</p>
<a class="abs btn" style="left:77px;top:986px;width:177px;height:62px">KNOW MORE</a>

<aside class="abs side-list">
  <div class="head">EXECUTIVE OFFICE SUITES</div>
  <ul>
    <li>ON- DEMAND MEETING ROOMS</li>
    <li>ON - DEMAND TRAINNING ROOMS</li>
    <li>VIRTUAL OFFICES SOLUTIONS</li>
    <li>VIDEO CONFERENCE SOLUTIONS</li>
  </ul>
</aside>

<section class="abs services"></section>
<h2 class="abs" style="left:0;width:1200px;top:1190px;text-align:center">OUR SERVICES</h2>
<p class="abs" style="left:0;width:1200px;top:1248px;text-align:center;font:400 16px/26px Arial,sans-serif;color:#555">Calloway Business Centers positions its management team in every one of its business centers -<br>we operate with an open-door policy as a medium-sized.</p>
<div class="abs video full" role="img" aria-label="Video thumbnail for full service executive office suites"></div>
<div class="abs video virtual" role="img" aria-label="Video thumbnail for virtual office services">
  <svg style="position:absolute;left:222px;top:78px" width="70" height="52" viewBox="0 0 70 52"><rect width="70" height="52" rx="8" fill="#07076b"/><path d="M27 14v24l19-12z" fill="#fff"/></svg>
</div>
<p class="abs caption" style="left:77px">Click here to watch an Informative video about <b>calloway's full services executive office Suites.</b></p>
<p class="abs caption" style="left:612px">Click here to watch an Informative video about <b>calloway's virtual office services.</b></p>

<h2 class="abs" style="left:79px;top:1700px">OUR VALUE</h2>
<p class="abs para" style="left:79px;top:1767px;width:650px">Either you need Dallas/Ft. Worth Office Space, Dallas Executive Suites, Ft. Worth Executive Suites, Houston Office Space, Houston Executive Suites, or maybe you simply need a place to stop in and use an on-demand office or meeting room from time to time or utilize our local business phone numbers, phone answering or business addresses through one of our virtual office solutions. At Calloway, you will always find affordable and beautiful, professional properties. To make decisions easy for our full service executive suite clients, we include everything in one upfront and honest price - including the office..</p>
<a class="abs btn" style="left:77px;top:1992px;width:177px;height:61px">KNOW MORE</a>

<form class="abs quote">
  <div class="head">GET A QUOTE</div>
  <div class="field" style="top:85px">Name *</div>
  <div class="field" style="top:138px">Email *</div>
  <div class="field" style="top:191px">Company *</div>
  <div class="field" style="top:244px">Phone *</div>
  <div class="btn submit">SUBMIT</div>
</form>

<footer class="abs footer"></footer>
<div class="abs foot-head" style="left:79px">CELEBRATING YEAR</div>
<div class="abs badge" role="img" aria-label="Anniversary badge marking years of service"></div>
<div class="abs foot-head" style="left:435px">USEFULL LINKS</div>
<ul class="abs links" style="left:435px">
  <li class="current">About us</li><li>Contact us</li><li>Testimonials</li><li>FAQs</li>
</ul>
<ul class="abs links" style="left:598px">
  <li class="marked">Careers</li><li>Specials</li><li>Site Map</li><li>Privacy</li>
</ul>
<div class="abs foot-head" style="left:812px">CONTACT INFO</div>
<div class="abs contact">
  <div class="row"><svg width="20" height="28" viewBox="0 0 20 28" fill="none" stroke="#07076b" stroke-width="1.8"><path d="M10 26s8-9 8-15a8 8 0 0 0-16 0c0 6 8 15 8 15z"/><circle cx="10" cy="11" r="3"/></svg><span>Calloway Business Centers 4120 N. Harwood Parkway Suite 300 Dallas, Texas 75219</span></div>
  <div class="row"><svg width="20" height="20" viewBox="0 0 24 24" fill="none" stroke="#07076b" stroke-width="1.8"><path d="M6.6 10.8a15 15 0 0 0 6.6 6.6l2.2-2.2c.3-.3.7-.4 1-.2 1.1.4 2.3.6 3.6.6.6 0 1 .4 1 1V20c0 .6-.4 1-1 1A17 17 0 0 1 3 4c0-.6.4-1 1-1h3.5c.6 0 1 .4 1 1 0 1.2.2 2.4.6 3.6.1.3 0 .7-.2 1z"/></svg><span>713.555.0147 &nbsp; Or &nbsp; 214.555.0190</span></div>
  <div class="row"><svg width="20" height="16" viewBox="0 0 20 16" fill="none" stroke="#07076b" stroke-width="1.8"><rect x="1" y="1" width="18" height="14"/><path d="M1 1l9 8 9-8"/></svg><span>Offices@CallowayOffices.com</span></div>
</div>

<div class="abs bottombar">
  <div class="copy">© 2016 <b>CALLOWAY BUSINESS CENTERS</b> All rights reserved.</div>
  <div class="social" aria-label="Social links"><span></span><span></span><span></span><span></span><span></span></div>
</div>

</body>
</html>
```